Tolvane Inc., a third party debt collection agency needs a Website

Tolvane needs a very basic website (3 basic pages) so that consumers can download forms, potential employees can get required EEO language and see potential jobs, and to show that they are a consumer friendly organization.

I've attached a list of requirements and wishes titled "Tolvane Website Specifications"

Target Market(s)

Consumers that need to repay their government loans; Tolvane will walk through the process to assist them.

Industry/Entity Type

Financial Service

Coding

Coded - Design and coding required

Number of Pages Required

1 page

Font styles to use
Sans Serif

Colors
0355a3

Requirements
Must have
• Tolvane Logo
• See document "Tolvane Website Specifications" for all requirements

```html
<!DOCTYPE html>
<html lang="en">
<head>
<meta charset="utf-8">
<title>Tolvane, Inc.</title>
<link href="https://fonts.googleapis.com/css2?family=Open+Sans:ital,wght@0,400;0,600;0,700;1,400&display=swap" rel="stylesheet">
<style>
:root{
  --navy:#27287a;
  --navy-dark:#1f2068;
  --red:#8b1a1a;
  --red-bright:#9c2020;
  --text:#333;
  --muted:#555;
  --rule:#e3e3e3;
  --white:#fff;
}
*{box-sizing:border-box;margin:0;padding:0}
html,body{width:940px;height:1200px;overflow:hidden}
body{position:relative;background:var(--white);font-family:'Open Sans',Arial,sans-serif;color:var(--text)}
.abs{position:absolute}

/* header */
.top-rule{left:0;top:0;width:940px;height:3px;background:var(--navy)}
.site-header{left:0;top:3px;width:940px;height:94px;background:var(--white)}
.brand{left:125px;top:50px;font-size:25px;font-weight:700;color:var(--red);letter-spacing:-.3px;display:flex;align-items:center;gap:8px}
.brand-dot{width:14px;height:14px;border-radius:50%;background:var(--red)}
.contact-strip{top:19px;font-size:10px;color:var(--muted);display:flex;align-items:center;gap:9px}
.ring{width:20px;height:20px;border:1.5px solid var(--red);border-radius:50%;display:flex;align-items:center;justify-content:center}
.main-nav{top:66px;left:340px;display:flex;font-size:10.2px;font-weight:600;color:#333;letter-spacing:.2px}
.main-nav span{position:absolute;white-space:nowrap}
.main-nav .active{color:var(--navy)}
.nav-swoosh{left:339px;top:81px}
.search-btn{left:783px;top:58px;width:28px;height:28px;border-radius:50%;background:var(--navy);display:flex;align-items:center;justify-content:center}

/* hero */
.hero{left:0;top:97px;width:940px;height:395px}
.hero-media{position:absolute;inset:0;background:linear-gradient(100deg,#6b5a4c 0%,#b7a592 22%,#d9d8d4 45%,#c8c8c4 70%,#a7a8a6 100%)}
.hero-band-title{left:600px;top:244px;width:340px;height:37px;background:rgba(70,70,70,.88);clip-path:polygon(0 0,100% 0,100% 100%,3% 100%);color:#fff;font-size:15px;font-weight:700;padding:10px 0 0 26px;letter-spacing:.2px}
.hero-band-text{left:440px;top:286px;width:500px;height:43px;background:rgba(110,110,110,.82);clip-path:polygon(2% 0,100% 0,100% 100%,0 100%);color:#fff;font-size:8.6px;font-weight:600;line-height:12.5px;padding:11px 20px 0 25px}

/* welcome */
.welcome-title{left:0;top:504px;width:940px;text-align:center;font-size:23.5px;font-weight:700;color:var(--navy)}
.welcome-title em,.section-title em{font-style:normal;color:var(--red)}
.welcome-copy{left:145px;top:545px;width:650px;text-align:center;font-size:8.3px;line-height:15.2px;color:#333}
.btn{display:flex;height:25px;font-size:8.4px;font-weight:600;color:#fff;letter-spacing:.2px}
.btn-label{background:var(--red);padding:0 10px;display:flex;align-items:center}
.btn-icon{background:var(--navy);width:24px;display:flex;align-items:center;justify-content:center}
.hr{left:125px;width:690px;height:1px;background:var(--rule)}

/* columns */
.section-title{font-size:18px;font-weight:700;color:var(--navy)}
.thumb{width:156px;height:131px;padding:3px;background:#fff;box-shadow:0 0 3px rgba(0,0,0,.35)}
.thumb div{width:100%;height:100%}
.col-copy{width:166px;font-size:8.3px;line-height:14.6px;color:#444;text-align:justify}

/* badges */
.badge{background:#4a82c8}
.badge-alt{background:#1d6279}

/* footer */
.site-footer{left:0;top:1015px;width:940px;height:144px;background:var(--navy)}
.footer-brand{left:125px;top:1080px;font-size:21px;font-weight:700;color:#fff;display:flex;align-items:center;gap:7px}
.footer-brand .brand-dot{background:#fff;width:12px;height:12px}
.vrule{top:1045px;width:1px;height:100px;background:rgba(255,255,255,.14)}
.footer-head{top:1045px;font-size:11.5px;font-weight:600;color:#fff}
.footer-list{font-size:8.6px;color:#fff;line-height:17px;list-style:none}
.contact-list{left:471px;top:1069px;font-size:8.3px;color:#fff;line-height:16px;list-style:none}
.contact-list li{display:flex;gap:9px;align-items:center}
.contact-list li.indent{padding-left:15px}
.email-field{left:642px;top:1072px;width:172px;height:29px;background:#fff;border:1px solid #ccc;font-size:8.2px;font-style:italic;color:#555;padding:9px 7px}
.submit-btn{left:642px;top:1104px;width:71px;height:27px;background:var(--red-bright);color:#fff;font-size:10px;font-weight:700;display:flex;align-items:center;justify-content:center;box-shadow:0 1px 2px rgba(0,0,0,.4)}
.legal{left:0;top:1159px;width:940px;height:41px;background:var(--red);color:#fff;font-size:8.3px;text-align:center;padding-top:15px}
</style>
</head>
<body>

<div class="abs top-rule"></div>
<header class="abs site-header"></header>
<div class="abs brand"><span class="brand-dot"></span>Tolvane, Inc.</div>

<div class="abs contact-strip" style="left:532px">
  <span class="ring"><svg width="9" height="7" viewBox="0 0 9 7"><rect width="9" height="7" rx="1" fill="#8b1a1a"/><path d="M0 1l4.5 3L9 1" stroke="#fff" fill="none"/></svg></span>
  Email: info@company.Com
</div>
<div class="abs contact-strip" style="left:692px">
  <span class="ring"><svg width="9" height="9" viewBox="0 0 10 10"><path d="M2 1l2 2-1 1.5c.6 1.2 1.3 1.9 2.5 2.5L7 6l2 2-1.3 1.5C4.5 9 1 5.5.5 2.3z" fill="#8b1a1a"/></svg></span>
  Phone: 000-000-0009
</div>

<nav class="abs main-nav">
  <span class="active" style="left:0">HOME</span>
  <span style="left:67px">CONSUMER INFORMATION</span>
  <span style="left:232px">CAREERS @ TOLVANE</span>
  <span style="left:375px">CONTACT</span>
</nav>
<svg class="abs nav-swoosh" width="34" height="8" viewBox="0 0 34 8"><path d="M1 5c8-5 14 4 32-2" stroke="#27287a" stroke-width="2" fill="none"/></svg>
<div class="abs search-btn"><svg width="9" height="9" viewBox="0 0 10 10"><circle cx="4" cy="4" r="3" stroke="#fff" stroke-width="1.6" fill="none"/><path d="M6.3 6.3L9 9" stroke="#fff" stroke-width="1.6"/></svg></div>

<section class="abs hero">
  <div class="hero-media" role="img" aria-label="Photo of smiling call-centre staff wearing headsets in a bright office"></div>
  <svg class="abs" style="left:0;top:0" width="940" height="395" viewBox="0 0 940 395">
    <path d="M48 158L34 178l14 20" stroke="#fff" stroke-width="1.3" fill="none" opacity=".85"/>
    <path d="M887 158l14 20-14 20" stroke="#fff" stroke-width="1.3" fill="none" opacity=".6"/>
    <rect x="834" y="273" width="24" height="2" fill="#b02020"/>
    <rect x="846" y="279" width="13" height="2" fill="#fff"/>
    <rect x="846" y="285" width="13" height="2" fill="#fff"/>
    <rect x="846" y="291" width="13" height="2" fill="#fff"/>
    <path d="M0 343C200 400 300 398 470 383S800 330 940 343V395H0Z" fill="#fff"/>
    <path d="M0 343C200 400 300 398 470 383S800 330 940 343" stroke="#27287a" stroke-width="4" fill="none"/>
  </svg>
  <div class="abs hero-band-title" style="top:147px">WELCOME TO TOLVANE</div>
  <div class="abs hero-band-text" style="top:189px">Lorem ipsum dolor sit amet, consectetur adipiscing elit, sed do eiusmod tempornc ididunt ut labore et dolore magna aliqua. Ut enim ad minim veniam.</div>
</section>

<h1 class="abs welcome-title">Welcome to <em>Tolvane</em></h1>
<p class="abs welcome-copy">Tolvane is a third party debt collection agency that is focused on the collection of higher education loans. Tolvane is compliant with all federal, state, and local laws and is committed to the professional and fair treatment of consumers. Our goal is to assist consumers in resolving their obligations in the manner that best meets their needs and to provide information necessary in order for consumers to make an informed decision. Sed ut perspiciatis unde omnis iste natus error sit voluptatem accusantium doloremque lauda ntim, totam rem aperiam, eaque ipsa quae ab illo invenue lauda ntim, totam rem aperitore veritatis et quasi archi.</p>
<div class="abs btn" style="left:426px;top:614px"><span class="btn-label">READ MORE</span><span class="btn-icon"><svg width="9" height="9" viewBox="0 0 10 10"><circle cx="5" cy="5" r="5" fill="#fff"/><path d="M4 3l2 2-2 2" stroke="#27287a" stroke-width="1.5" fill="none"/></svg></span></div>

<div class="abs hr" style="top:662px"></div>

<h2 class="abs section-title" style="left:125px;top:682px">Consumer <em>Information</em></h2>
<div class="abs thumb" style="left:127px;top:717px"><div role="img" aria-label="Photo of colleagues reviewing documents at a meeting table" style="background:linear-gradient(135deg,#8c97a6,#d8d4cc 55%,#5c6674)"></div></div>
<p class="abs col-copy" style="left:296px;top:720px">Sed ut perspiciatis unde omnis iste natus error sit voluptatem accusantium dolo-remque laudantium, totam rem aperiam, ea que ipsa quae ab illo inventore veritatis et quasi architectobea tae vitae dicta sunt explicaboemo enim ipsam volupta</p>
<div class="abs btn" style="left:296px;top:817px"><span class="btn-label">READ MORE</span><span class="btn-icon"><svg width="9" height="9" viewBox="0 0 10 10"><circle cx="5" cy="5" r="5" fill="#fff"/><path d="M4 3l2 2-2 2" stroke="#27287a" stroke-width="1.5" fill="none"/></svg></span></div>

<h2 class="abs section-title" style="left:479px;top:682px">Careers @ <em>Tolvane</em></h2>
<div class="abs thumb" style="left:481px;top:717px"><div role="img" aria-label="Photo of two business professionals in suits in an office" style="background:linear-gradient(120deg,#2f4a72,#9aa9bc 45%,#e4e2de)"></div></div>
<p class="abs col-copy" style="left:649px;top:720px">Sed ut perspiciatis unde omnis iste natus error sit voluptatem accusantium dolo-remque laudantium, totam rem aperiam, ea que ipsa quae ab illo inventore veritatis et quasi architectobea tae vitae dicta sunt explicaboemo enim ipsam volupta</p>
<div class="abs btn" style="left:649px;top:817px"><span class="btn-label">READ MORE</span><span class="btn-icon"><svg width="9" height="9" viewBox="0 0 10 10"><circle cx="5" cy="5" r="5" fill="#fff"/><path d="M4 3l2 2-2 2" stroke="#27287a" stroke-width="1.5" fill="none"/></svg></span></div>

<div class="abs hr" style="top:869px"></div>

<div class="abs badge" role="img" aria-label="Trade association membership badge" style="left:393px;top:894px;width:46px;height:46px"></div>
<div class="abs badge-alt" role="img" aria-label="Business accreditation badge" style="left:490px;top:885px;width:62px;height:106px;border-radius:4px"></div>

<footer class="abs site-footer"></footer>
<div class="abs footer-brand"><span class="brand-dot"></span>Tolvane, Inc.</div>
<div class="abs vrule" style="left:297px"></div>
<div class="abs vrule" style="left:444px"></div>
<div class="abs vrule" style="left:614px"></div>

<div class="abs footer-head" style="left:318px">NAVIGATION</div>
<ul class="abs footer-list" style="left:319px;top:1069px">
  <li>Home</li><li>Consumer Information</li><li>Careers @ Tolvane</li><li>Contact</li>
</ul>

<div class="abs footer-head" style="left:471px">CONTACT US</div>
<ul class="abs contact-list">
  <li><svg width="6" height="8" viewBox="0 0 6 8"><path d="M3 0a3 3 0 0 1 3 3c0 2-3 5-3 5S0 5 0 3a3 3 0 0 1 3-3z" fill="#fff"/><circle cx="3" cy="3" r="1" fill="#27287a"/></svg>201 lorem ipsum dolor site,</li>
  <li class="indent">tolvane dummy text,5482</li>
  <li><svg width="7" height="7" viewBox="0 0 10 10"><path d="M2 1l2 2-1 1.5c.6 1.2 1.3 1.9 2.5 2.5L7 6l2 2-1.3 1.5C4.5 9 1 5.5.5 2.3z" fill="#fff"/></svg>Phone:&nbsp; 000-555-0143</li>
  <li><svg width="7" height="6" viewBox="0 0 9 7"><rect width="9" height="7" fill="#fff"/><path d="M0 1l4.5 3L9 1" stroke="#27287a" fill="none"/></svg>info@company.com</li>
</ul>

<div class="abs footer-head" style="left:641px">NEWSLETTER</div>
<div class="abs email-field">Email Address:</div>
<div class="abs submit-btn">SUBMIT</div>

<div class="abs legal">© 2016 Tolvane. All copyrights are reserved&nbsp; Term of Use, Privay Policy</div>

</body>
</html>
```